2 x Digitize Logo | 2 x Business Cards | 2 x Fridge Magnets

We require 6 deliverables:
1. Residential logo redrawn (same just high quality for large print format).
2. Corporate logo redrawn (minor changes to wording and high quality for large print format).
3. New business card design for Furniture Removals (residential)
4. New business card design for Corporate Relocations (business)
5. New Fridge magnet for Furniture removals (residential)
6. New fridge magnet for Corporate Relocations (business)
1. Residential Logo
a. We require the logo to be translated into a high quality digital image with no modifications.
(see attached resilogo.jpg)
2. Residential Logo
a. We require the logo to be edited (add the word corporate relocations) be translated into a high quality digital image.
(see attached corplogo.jpg)
3. Using the resilogo please make a new business card for our business.
a. Please see the web site https://www.larkbendcarters.com.au for colours and inspiration.
b. The residential business card needs the following information:
i. Business Name (using the residential logo).
ii. Free Call: 1800 LB Cart (the L, B and Cart much be the same colour as the logo).
iii. Website: www.LarkbendCarters.com.au
iv. Address: 4/17 Ormsdale Court, VIC 3264
v. Email: cart@LarkbendCarters.com.au
vi. backof Card:
Review our service
www.PennantOrbit.com.au
Services: Local, Country, Interstate | Furniture Removals | Piano, Billiard Tables & Antiques
4. Using the corplogo please make a new business card for our business.
b. The corporate business card needs the following information:
i. Business Name (using the corporate logo).
v. Email: corporate@LarkbendCarters.com.au
vi. Back of Card:
Review our service
www.PennantOrbit.com.au
Services: Corporate relocations | Office equipment moves | Packing Service | Packing Materials
5. Using the resilogo please make a new fridge magent for our business.
b. The residential fidge magnet needs the following information:
iv. Services: Local, Country, Interstate | Furniture Removals | Piano, Billiard Tables & Antiques
6. Using the corplogo please make a new fridge magent for our business.
b. The corporate fidge magnet needs the following information:
iv. Services: Local, Country, Interstate | Corporate relocations
Target Market(s)
Residential Furniture Removals and Corporate Office relocations
Industry/Entity Type
Business
Contact Information for Business Card
Please see full brief for six items required
Requirements
Must have
- Clean simple, easy to read
Nice to have
- fresh, stand out, eye catching
Should not have
- plain, standard, boring, general

```html
<!DOCTYPE html>
<html lang="en">
<head>
<meta charset="utf-8">
<title>Larkbend Carters – Business Card</title>
<link rel="stylesheet" href="https://fonts.googleapis.com/css2?family=Catamaran:wght@400;500;700;800&display=swap">
<style>
  :root {
    --page: #e4e0dc;
    --card: #f4f4f3;
    --green: #22b14c;
    --yellow: #f7c400;
    --red: #e42421;
    --ink: #1d1d1d;
    --white: #ffffff;
  }
  * { box-sizing: border-box; margin: 0; padding: 0; }
  html, body { width: 1109px; height: 1200px; overflow: hidden; }
  body {
    background: var(--page);
    font-family: "Catamaran", "Helvetica Neue", Arial, sans-serif;
    color: var(--ink);
    position: relative;
  }
  .card-slot { position: absolute; left: 114px; width: 880px; height: 544px; }
  .card-slot.front { top: 36px; }
  .card-slot.back { top: 620px; }
  .card {
    position: absolute; top: 0; left: 0;
    width: 652px; height: 403px;
    transform: scale(1.35); transform-origin: 0 0;
    background: var(--card);
    overflow: hidden;
    box-shadow: 0 2px 8px rgba(0,0,0,.12);
  }
  .card-shape { position: absolute; inset: 0; width: 652px; height: 403px; }

  .brand-name {
    position: absolute; top: 80px; left: 244px; width: 380px;
    text-align: right;
    font-weight: 800; font-size: 37px; line-height: 1;
    letter-spacing: .5px;
    color: var(--green);
  }

  .services { position: absolute; left: 35px; top: 256px; color: var(--white); }
  .services-title { font-size: 20px; font-weight: 400; letter-spacing: .3px; margin-bottom: 12px; line-height: 1; }
  .services-list { list-style: none; font-size: 17px; line-height: 24px; }
  .services-list li::before {
    content: ""; display: inline-block; width: 8px; height: 8px;
    border-radius: 50%; background: var(--white);
    margin-right: 6px; vertical-align: 2px;
  }

  .contact { position: absolute; right: 24px; top: 266px; text-align: right; font-size: 17px; }
  .contact-line { display: flex; justify-content: flex-end; align-items: center; gap: 5px; height: 24px; }
  .contact-line.address { margin-top: 7px; }
  .contact-line svg { width: 13px; height: 13px; flex: none; }
  .hl-yellow { color: var(--yellow); font-weight: 500; }
  .hl-green { color: var(--green); font-weight: 500; }

  .review { position: absolute; left: 377px; top: 318px; color: var(--white); }
  .review-title { font-size: 17px; font-weight: 700; letter-spacing: .2px; line-height: 24px; }
  .review-url { font-size: 17px; line-height: 26px; }
</style>
</head>
<body>

<div class="card-slot front">
  <section class="card card-front" aria-label="Business card front">
    <svg class="card-shape" viewBox="0 0 652 403" aria-hidden="true">
      <polygon points="0,0 270,0 198,58 340,403 0,403" fill="var(--green)"/>
      <polyline points="276,0 203,58 346,403" fill="none" stroke="var(--red)" stroke-width="4"/>
      <polyline points="283,0 209,58 352,403" fill="none" stroke="var(--yellow)" stroke-width="4"/>
    </svg>

    <div class="brand-name">LARKBEND CARTERS</div>

    <div class="services">
      <h2 class="services-title">SERVICES</h2>
      <ul class="services-list">
        <li>Local, Country, Interstate</li>
        <li>Furniture Removals</li>
        <li>Piano, Billiard Tables &amp; Antiques</li>
      </ul>
    </div>

    <div class="contact">
      <div class="contact-line">
        <span>1800 <span class="hl-yellow">LB</span> <span class="hl-green">Cart</span> / 1800 52 40 19</span>
        <svg viewBox="0 0 16 16"><path fill="var(--green)" d="M3.5 1.5l2.4-.4 1.4 3.4-1.6 1.3c.8 1.7 2 2.9 3.7 3.8l1.3-1.6 3.4 1.4-.4 2.4c-.2.9-1 1.4-1.9 1.3C6.6 12.6 3.3 9.4 2.3 3.4c-.1-.9.4-1.7 1.2-1.9z"/></svg>
      </div>
      <div class="contact-line">
        <span>cart@LarkbendCarters.com.au</span>
        <svg viewBox="0 0 16 16"><rect x="1" y="3" width="14" height="10" fill="var(--green)"/><polyline points="1.5,3.5 8,9 14.5,3.5" fill="none" stroke="var(--white)" stroke-width="1.3"/></svg>
      </div>
      <div class="contact-line">
        <span>www.LarkbendCarters.com.au</span>
        <svg viewBox="0 0 16 16"><circle cx="8" cy="8" r="7" fill="var(--green)"/><path d="M4 6c1.5-1 2.5 0 3 1.5S9 9 8 11M10 3.5c.5 1.5 2 2 3 1.8" fill="none" stroke="var(--white)" stroke-width="1.3"/></svg>
      </div>
      <div class="contact-line address">
        <span>4/17 Ormsdale Court, VIC 3264</span>
        <svg viewBox="0 0 16 16"><path fill="var(--green)" d="M8 0.5a5.5 5.5 0 0 1 5.5 5.5c0 4-5.5 9.5-5.5 9.5S2.5 10 2.5 6A5.5 5.5 0 0 1 8 .5z"/><circle cx="8" cy="6" r="2" fill="var(--white)"/></svg>
      </div>
    </div>
  </section>
</div>

<div class="card-slot back">
  <section class="card card-back" aria-label="Business card back">
    <svg class="card-shape" viewBox="0 0 652 403" aria-hidden="true">
      <polygon points="382,0 652,0 652,403 312,403 454,58" fill="var(--green)"/>
      <polyline points="376,0 449,58 306,403" fill="none" stroke="var(--red)" stroke-width="4"/>
      <polyline points="369,0 443,58 300,403" fill="none" stroke="var(--yellow)" stroke-width="4"/>
    </svg>

    <div class="review">
      <h2 class="review-title">REVIEW OUR SERVICE</h2>
      <p class="review-url">www.PennantOrbit.com.au</p>
    </div>
  </section>
</div>

</body>
</html>
```